Wine Label Design-Hollow Creek Vineyard

Hollow Creek Vineyard is in the Barossa Valley in South Australia. The Barossa is recognized as Australia's premier wine region, producing Australia's icon wines and some " new takes on traditional".
This family owned and operated vineyard grows some exceptionally high quality fruit. Most of the fruit is sold and used for some of Australia's most iconic wines. Small quantities are retained by the owners for some wines with very limited availability. (Wines were previously sold as Brackwell Vineyards Hollow Creek ( Shiraz, Cabernet etc).

The wines will in the future be labeled simply ‘Hollow Creek Vineyard’. The label will launch this new identity for the single family single vineyard and its high quality wines which are a true expression of the vineyard and derive from the Hollow Creek common to this ancient area (800-2000 million years old).
The label should reflect
• Single vineyard, family owned
• vines in very old rock & soils
• High quality & reliability
• Edgy but true, design based thinking (Please note:blue is generally seen as an unacceptable colour for a wine label?? Don’t ask me why)

The wines will be sold mostly direct in Australia ( ie not through retail stores), with limited export to Asia, Scandinavia and Canada.
There are three quality levels and price points in the portfolio
1. Entry level premium for everyday drinking for discriminating drinkers-approx AUD20
2. Super Premium-approx AUD30
3. Limited Release ultlra premium-AUD75-90?
We envisage three variations on the label but with an obvious & common design element. This design element should be able to be used for corporate identification and promotion
The paper stock will be waterproof and self adhesive. Our preference is for designs that engage the user by appealing to both sight and touch. It is preferred that textures be added eg embossing, high build varnish etc-rather than be a facet of the stock itself.
For information on statutory label requirements refer to www.vintnerregistry-example.com . In brief
o Front label need not show any mandatory information. However we would prefer Variety, Barossa Valley, Year and alcohol to be shown on the front label
o Back label should show all mandatories and allow for a bar code
Updates

Project Deadline Extended
Reason: I've had a problem with my wireless broadband account and reception has been intermittent to say the least to the extent that I switched off at the weekend. Just going downtown now for a 'polite discussion' with my service provider.

Project Deadline Extended
Reason: I have receiver insufficient designs of quality which we would consider. Too many designs have a "cut and paste" appearance - too few exhibit an original art/design element which truly identifies the product.

Gals & Guys

most of the designs submitted lack punch and originality and are totally unmemorable.
Please-get on Searcho or whatever enter "Wine Label Designs" and do some research b4 u waste your time and mine. Formulaic cut and paste will not win the day. That's not to say that cut and paste can't work-but it must have some originality, impact and command attention. Please surprise me.

Following on from a question from a designer about who is our competition and what we are looking for I sent the following 
"I don't think I can add anything new. Read the brief and comments again and research wine labels on the web. In 30 minutes you'll get a good idea of the creative edgy designs in the industry. There are a plethora of collections. Our competition-anyone with a label. In 2010 there were over 2400 "producers" in other words 2400 producers with at least one label. In fact there are over 25000 Australian wines and then the numerous imported wines.

Target Market(s)

$20 people who budget everyday but have graduated from drinking 'entry level' wines. These people will likely fit into Cat. (b) in the $30 wine

$30 (a) will not over-compromise on some everyday discretionary expenditure.(b) might buy for special occasions

$70-$90 Professional/successful people with high disposable/discretionary income not particularly worried about recession. wine geeks.

Industry/Entity Type

Retail

Requirements
Must have
• identifiable element across range of wines

```html
<!DOCTYPE html>
<html lang="en">
<head>
<meta charset="utf-8">
<title>Hollow Creek Vineyard – Label Range</title>
<link rel="stylesheet" href="https://fonts.googleapis.com/css2?family=Gelasio:ital,wght@0,400;0,700;1,400;1,700&display=swap">
<style>
  :root{
    --paper:#ffffff;
    --cream:#f6f5e6;
    --ink:#1d1d1d;
    --stone-light:#dcdcdc;
    --stone-mid:#ababab;
    --stone-dark:#707070;
    --shiraz:#7c1b28;
    --grenache:#1f4a2d;
    --cabernet:#c0212b;
    --shiraz-back:#7b1f2c;
    --grenache-back:#1d4a2c;
    --cabernet-back:#b81f29;
    --on-dark:#ffffff;
  }
  *{box-sizing:border-box;margin:0;padding:0}
  html,body{width:839px;height:1200px;overflow:hidden;background:var(--paper)}
  body{position:relative;font-family:"Gelasio",Georgia,serif;color:var(--ink)}

  .column-heading{position:absolute;top:2px;font-size:28px;font-weight:400;width:200px;text-align:center}
  .column-heading--front{left:378px}
  .column-heading--back{left:618px}

  /* Front label */
  .front-label{position:absolute;width:245px;height:327px;--s:1;--accent:var(--shiraz)}
  .front-label--hero{left:34px;top:496px;width:218px;height:420px;--s:1.12}
  .front-label--grenache{--accent:var(--grenache)}
  .front-label--cabernet{--accent:var(--cabernet)}
  .stone-frame{position:absolute;inset:0;
    background:linear-gradient(135deg,var(--stone-light) 0%,var(--stone-mid) 35%,var(--stone-light) 55%,var(--stone-dark) 80%,var(--stone-mid) 100%)}
  .label-panel{position:absolute;inset:8% 9% 8% 9%;background:var(--cream)}
  .label-panel > *{position:absolute;left:0;right:0;text-align:center}
  .wordmark{top:13%;line-height:1}
  .wordmark__name{display:inline-block;font-weight:700;font-size:calc(var(--s)*15px);padding:0 4px 2px;border-bottom:1.5px solid var(--accent)}
  .wordmark__sub{display:block;font-style:italic;font-size:calc(var(--s)*8px);margin-top:2px}
  .variety{top:40%;font-size:calc(var(--s)*24px);line-height:1;color:var(--accent)}
  .region{top:53%;font-style:italic;font-size:calc(var(--s)*8.5px)}
  .vintage{top:73%;font-size:calc(var(--s)*13px)}
  .alcohol{top:90%;font-size:calc(var(--s)*7px)}

  /* Back label */
  .back-label{position:absolute;left:652px;width:133px;height:272px;color:var(--on-dark);text-align:center;padding:8px 8px 0}
  .back-label--shiraz{top:84px;background:var(--shiraz-back)}
  .back-label--grenache{top:481px;background:var(--grenache-back)}
  .back-label--cabernet{top:840px;background:var(--cabernet-back)}
  .back-wordmark{line-height:1}
  .back-wordmark__name{display:inline-block;font-weight:700;font-size:11px;padding:0 6px 2px;border-bottom:1px solid var(--on-dark)}
  .back-wordmark__sub{display:block;font-style:italic;font-size:6px;margin-top:2px}
  .back-story{margin-top:8px;font-style:italic;font-weight:700;font-size:6.4px;line-height:1.3}
  .back-variety{margin-top:14px;font-size:17px;line-height:1}
  .back-region{font-style:italic;font-size:6px;margin-top:3px}
  .back-vintage{font-size:15px;margin-top:2px}
  .back-compliance{display:flex;justify-content:flex-end;align-items:center;gap:4px;margin-top:8px;height:44px}
  .std-drinks{writing-mode:vertical-rl;transform:rotate(180deg);font-size:5.5px;font-weight:700;white-space:nowrap}
  .warning-icon{width:28px;height:40px}
  .back-producer{position:absolute;left:0;right:0;bottom:18px;font-style:italic;font-weight:700;font-size:5px}
  .back-address{position:absolute;left:0;right:0;bottom:8px;font-style:italic;font-weight:700;font-size:4.6px}
</style>
</head>
<body>
  <h2 class="column-heading column-heading--front">Front</h2>
  <h2 class="column-heading column-heading--back">Back</h2>

  <section class="front-label front-label--hero">
    <div class="stone-frame" role="img" aria-label="Border of grey broken rock shards"></div>
    <div class="label-panel">
      <p class="wordmark"><span class="wordmark__name">Hollow Creek</span><span class="wordmark__sub">Vineyard</span></p>
      <p class="variety">Shiraz</p>
      <p class="region">Barossa Valley</p>
      <p class="vintage">2012</p>
      <p class="alcohol">13.5% alcohol</p>
    </div>
  </section>

  <section class="front-label" style="left:356px;top:56px">
    <div class="stone-frame" role="img" aria-label="Border of grey broken rock shards"></div>
    <div class="label-panel">
      <p class="wordmark"><span class="wordmark__name">Hollow Creek</span><span class="wordmark__sub">Vineyard</span></p>
      <p class="variety">Shiraz</p>
      <p class="region">Barossa Valley</p>
      <p class="vintage">2012</p>
      <p class="alcohol">13.5% alcohol</p>
    </div>
  </section>

  <section class="front-label front-label--grenache" style="left:356px;top:441px">
    <div class="stone-frame" role="img" aria-label="Border of grey broken rock shards"></div>
    <div class="label-panel">
      <p class="wordmark"><span class="wordmark__name">Hollow Creek</span><span class="wordmark__sub">Vineyard</span></p>
      <p class="variety">Grenache</p>
      <p class="region">Barossa Valley</p>
      <p class="vintage">2012</p>
      <p class="alcohol">13.5% alc/vol.</p>
    </div>
  </section>

  <section class="front-label front-label--cabernet" style="left:356px;top:811px">
    <div class="stone-frame" role="img" aria-label="Border of grey broken rock shards"></div>
    <div class="label-panel">
      <p class="wordmark"><span class="wordmark__name">Hollow Creek</span><span class="wordmark__sub">Vineyard</span></p>
      <p class="variety">Cabernet</p>
      <p class="region">Barossa Valley</p>
      <p class="vintage">2012</p>
      <p class="alcohol">13.5% alcohol</p>
    </div>
  </section>

  <section class="back-label back-label--shiraz">
    <p class="back-wordmark"><span class="back-wordmark__name">Hollow Creek</span><span class="back-wordmark__sub">Vineyard</span></p>
    <p class="back-story">Brackwell is a family owned Swiss-Australian joint venture. It's portfolio are two vineyards, REDGUM and HILLTOP, of a total of 32 hectares of planted vines.</p>
    <p class="back-variety">Shiraz</p>
    <p class="back-region">Barossa Valley</p>
    <p class="back-vintage">2012</p>
    <div class="back-compliance">
      <span class="std-drinks">Contains 8 std drinks</span>
      <svg class="warning-icon" viewBox="0 0 30 42" role="img" aria-label="Wine glass warning symbol"><rect width="30" height="42" fill="#fff"/><path d="M9 8h12l-1 12a5 5 0 0 1-10 0z M15 25v9 M10 34h10" fill="none" stroke="#000" stroke-width="1.6"/></svg>
    </div>
    <p class="back-producer">Produced by Hollow Creek Vineyards</p>
    <p class="back-address">Lot 1 Stonebank Road, Ironvale SA 5399, Australia</p>
  </section>

  <section class="back-label back-label--grenache">
    <p class="back-wordmark"><span class="back-wordmark__name">Hollow Creek</span><span class="back-wordmark__sub">Vineyard</span></p>
    <p class="back-story">Brackwell is a family owned Swiss-Australian joint venture. It's portfolio are two vineyards, REDGUM and HILLTOP, of a total of 32 hectares of planted vines.</p>
    <p class="back-variety">Grenache</p>
    <p class="back-region">Barossa Valley</p>
    <p class="back-vintage">2012</p>
    <div class="back-compliance">
      <span class="std-drinks">Contains 8 std drinks</span>
      <svg class="warning-icon" viewBox="0 0 30 42" role="img" aria-label="Wine glass warning symbol"><rect width="30" height="42" fill="#fff"/><path d="M9 8h12l-1 12a5 5 0 0 1-10 0z M15 25v9 M10 34h10" fill="none" stroke="#000" stroke-width="1.6"/></svg>
    </div>
    <p class="back-producer">Produced by Hollow Creek Vineyards</p>
    <p class="back-address">Lot 1 Stonebank Road, Ironvale SA 5399, Australia</p>
  </section>

  <section class="back-label back-label--cabernet">
    <p class="back-wordmark"><span class="back-wordmark__name">Hollow Creek</span><span class="back-wordmark__sub">Vineyard</span></p>
    <p class="back-story">Brackwell is a family owned Swiss-Australian joint venture. It's portfolio are two vineyards, REDGUM and HILLTOP, of a total of 32 hectares of planted vines.</p>
    <p class="back-variety">Cabernet</p>
    <p class="back-region">Barossa Valley</p>
    <p class="back-vintage">2012</p>
    <div class="back-compliance">
      <span class="std-drinks">Contains 8 std drinks</span>
      <svg class="warning-icon" viewBox="0 0 30 42" role="img" aria-label="Wine glass warning symbol"><rect width="30" height="42" fill="#fff"/><path d="M9 8h12l-1 12a5 5 0 0 1-10 0z M15 25v9 M10 34h10" fill="none" stroke="#000" stroke-width="1.6"/></svg>
    </div>
    <p class="back-producer">Produced by Hollow Creek Vineyards</p>
    <p class="back-address">Lot 1 Stonebank Road, Ironvale SA 5399, Australia</p>
  </section>
</body>
</html>
```